New Business Card for our Indoor Golf Training Facility

We are looking for designs for a new business card for our indoor golf training facility. Attached is our logo, our logo with our slogan, and here is our elevator pitch (What makes us different from the others) not sure if all the info will fit on one card, maybe you can condense the elevator pitch? here is the info

Elevator Pitch
We work with serious golfers and those that want to be serious golfers…
to make you better, faster, at all phases of the game…
We use the same state-of-the-art technology as professional golfers…
which produces data sets that shows your improvement in real time.
Our facility is available 24/7 to our members, which allows you to improve on your time.

our website: www.birchpinlinks.com

Target Market(s)

Golfers

Font styles to use
Serif
Sans Serif

Colors
ec1f27
f59195
fbd4d5
919191
d3d3d3
1b1b1b

Requirements
Must have
• our logo or our logo with the slogan, elevator pitch (can be condensed or shortened)

```html
<!DOCTYPE html>
<html lang="en">
<head>
<meta charset="utf-8">
<title>Birch Pin Links – Business Card</title>
<link rel="stylesheet" href="https://fonts.googleapis.com/css2?family=Roboto:wght@400;500;700;900&family=Open+Sans:ital,wght@1,600&display=swap">
<style>
  :root {
    --red: #ec1f27;
    --red-soft: #f59195;
    --ink: #1b1b1b;
    --grey: #919191;
    --grey-light: #d3d3d3;
    --paper: #ffffff;
    --backdrop: #ececec;
  }
  * { box-sizing: border-box; margin: 0; padding: 0; }
  html, body { width: 1200px; height: 911px; overflow: hidden; }
  body {
    background: var(--backdrop);
    font-family: "Roboto", Arial, sans-serif;
    display: flex;
    flex-direction: column;
    align-items: center;
    justify-content: center;
    gap: 40px;
  }
  .card {
    position: relative;
    width: 700px;
    height: 400px;
    background: var(--paper);
    border-radius: 22px;
    overflow: hidden;
    box-shadow: 0 4px 14px rgba(0,0,0,.12);
  }

  /* Front */
  .brand {
    position: absolute;
    left: 56px;
    top: 62px;
    display: flex;
    align-items: center;
    gap: 18px;
  }
  .brand-dot {
    width: 62px; height: 62px;
    border: 5px solid var(--red);
    border-radius: 50%;
    flex: none;
  }
  .brand-name {
    font-weight: 900;
    font-size: 58px;
    line-height: 1;
    color: var(--red);
    letter-spacing: -0.5px;
  }
  .slogan {
    position: absolute;
    left: 138px;
    top: 132px;
    font-size: 21px;
    color: var(--red);
  }
  .person {
    position: absolute;
    left: 300px;
    top: 178px;
  }
  .person-name {
    font-weight: 700;
    font-size: 30px;
    color: var(--red);
  }
  .person-title {
    font-weight: 500;
    font-size: 17px;
    color: var(--ink);
    margin-left: 36px;
  }
  .band-address {
    position: absolute;
    left: 0; bottom: 0;
    width: 320px; height: 122px;
    background: var(--red);
    color: #fff;
    padding: 22px 0 0 40px;
    font-size: 17px;
    font-style: normal;
    line-height: 1.45;
  }
  .band-contact {
    position: absolute;
    right: 0; bottom: 0;
    width: 380px; height: 150px;
    background: var(--ink);
    color: #fff;
    padding: 30px 28px 0 0;
    font-size: 17px;
    line-height: 1.9;
  }
  .contact-row {
    display: flex;
    justify-content: flex-end;
    align-items: center;
    gap: 10px;
  }
  .contact-row svg { width: 15px; height: 15px; fill: var(--red); flex: none; }

  /* Back */
  .back-mark {
    position: absolute;
    left: 0; right: 0;
    top: 46px;
    display: flex;
    flex-direction: column;
    align-items: center;
    gap: 10px;
  }
  .back-dot {
    width: 78px; height: 78px;
    border: 6px solid var(--red);
    border-radius: 50%;
  }
  .back-name {
    font-weight: 700;
    font-size: 22px;
    color: var(--red);
  }
  .pitch-title {
    position: absolute;
    top: 188px;
    width: 100%;
    text-align: center;
    font-weight: 700;
    font-size: 22px;
    color: var(--red);
  }
  .pitch {
    position: absolute;
    top: 226px;
    left: 40px; right: 40px;
    text-align: center;
    font-family: "Open Sans", Arial, sans-serif;
    font-style: italic;
    font-weight: 600;
    font-size: 14px;
    line-height: 1.55;
    color: #555;
  }
</style>
</head>
<body>

  <section class="card card-front">
    <div class="brand">
      <span class="brand-dot"></span>
      <span class="brand-name">Birch Pin Links</span>
    </div>
    <p class="slogan">Play Smart. Swing True. Score Lower.</p>
    <div class="person">
      <p class="person-name">Dana Hollis</p>
      <p class="person-title">CEO/Founder</p>
    </div>
    <address class="band-address">
      1480 W. Alder Rd.<br>Unit B4 Maple Falls<br>OH 45000
    </address>
    <div class="band-contact">
      <p class="contact-row">555-210-4478
        <svg viewBox="0 0 24 24"><path d="M6.6 10.8a15 15 0 0 0 6.6 6.6l2.2-2.2c.3-.3.7-.4 1-.2 1.1.4 2.3.6 3.6.6.6 0 1 .4 1 1V20c0 .6-.4 1-1 1A17 17 0 0 1 3 4c0-.6.4-1 1-1h3.5c.6 0 1 .4 1 1 0 1.3.2 2.5.6 3.6.1.3 0 .7-.2 1z"/></svg>
      </p>
      <p class="contact-row">info@birchpinlinks.com
        <svg viewBox="0 0 24 24"><path d="M2 5h20v14H2z"/><path d="M3 6l9 7 9-7" stroke="#1b1b1b" stroke-width="2" fill="none"/></svg>
      </p>
      <p class="contact-row">birchpinlinks.com
        <svg viewBox="0 0 24 24"><circle cx="12" cy="12" r="10"/><path d="M2 12h20M12 2c3 3 3 17 0 20M12 2c-3 3-3 17 0 20" stroke="#1b1b1b" stroke-width="1.6" fill="none"/></svg>
      </p>
    </div>
  </section>

  <section class="card card-back">
    <div class="back-mark">
      <span class="back-dot"></span>
      <span class="back-name">Birch Pin Links</span>
    </div>
    <h2 class="pitch-title">ELEVATOR PITCH:</h2>
    <p class="pitch">
      We work with serious golfers and those that want to be serious golfers…<br>
      to make you better, faster, at all phases of the game…<br>
      We use the same state-of-the-art technology as professional golfers…<br>
      which produces data sets that shows your improvement in real time.<br>
      Our facility is available 24/7 to our members, which allows you to improve on your time.
    </p>
  </section>

</body>
</html>
```